Small Business Broker Business Card Design

A business card design for a small business brokerage, which is a financial service, not unlike real estate brokerage, but for small businesses such as laundromats, pizza shops, restaurants, cleaners etc. The designs should all be simple, more conservative in nature, using the colors and font of the logo. Again, think real estate Brokerage as a business context
Contact Information for Business Card
Name: Glen R. Harlow. Title: Small Business Advisor. Email: g.harlow@bayfieldcapitalworks.example. Mobile: (555) 274-3918. Office: (555) 806-2147. www.bayfieldcapitalworks.example

```html
<!DOCTYPE html>
<html lang="en">
<head>
<meta charset="utf-8">
<title>Bayfield Capital Works — Business Card</title>
<link href="https://fonts.googleapis.com/css2?family=Montserrat:wght@600;700;800&family=Arimo:wght@400&display=swap" rel="stylesheet">
<style>
  :root {
    --stage: #151515;
    --navy: #1b3a6e;
    --navy-deep: #142d58;
    --green: #8dc63f;
    --white: #ffffff;
    --ink: #5a5a5a;
  }
  * { box-sizing: border-box; margin: 0; padding: 0; }
  html, body {
    width: 1200px; height: 963px; overflow: hidden;
    background: var(--stage);
  }
  .canvas { position: relative; width: 1200px; height: 963px; }

  .card {
    position: absolute;
    width: 580px; height: 331px;
    border-radius: 22px;
    overflow: hidden;
  }

  /* Front */
  .card--front { left: 80px; top: 90px; background: var(--white); padding: 34px 36px; }
  .company {
    font-family: "Montserrat", sans-serif; font-weight: 800;
    text-transform: uppercase; letter-spacing: 0.06em;
    color: var(--navy); font-size: 19px; line-height: 1.1;
  }
  .tagline {
    font-family: "Montserrat", sans-serif; font-weight: 700;
    text-transform: uppercase; letter-spacing: 0.08em;
    color: var(--green); font-size: 9px; margin-top: 3px;
  }
  .person { margin-top: 30px; }
  .person__name {
    font-family: "Montserrat", sans-serif; font-weight: 800;
    text-transform: uppercase; letter-spacing: 0.03em;
    color: var(--navy); font-size: 22px;
  }
  .person__title {
    font-family: "Arimo", sans-serif; color: var(--green);
    font-size: 13px; margin-top: 2px;
  }
  .contacts { list-style: none; margin-top: 24px; }
  .contacts li {
    display: flex; align-items: center; gap: 9px;
    font-family: "Arimo", sans-serif; color: var(--ink);
    font-size: 12.5px; line-height: 1.55;
  }
  .contacts svg { width: 12px; height: 12px; flex: none; }
  .brand-graphic {
    position: absolute; right: 0; bottom: 0;
    width: 250px; height: 220px;
    background: linear-gradient(135deg, rgba(141,198,63,0.15), rgba(27,58,110,0.35));
    border-top-left-radius: 200px 200px;
  }

  /* Back */
  .card--back {
    left: 540px; top: 520px;
    background: linear-gradient(160deg, var(--navy) 0%, var(--navy-deep) 100%);
    display: flex; align-items: center; justify-content: center;
  }
  .lockup { display: flex; align-items: center; gap: 16px; }
  .lockup__square { width: 34px; height: 34px; background: var(--green); flex: none; }
  .lockup .company { color: var(--white); font-size: 20px; }
</style>
</head>
<body>
<main class="canvas">

  <section class="card card--front" aria-label="Business card front">
    <h1 class="company">Bayfield Capital Works, Inc</h1>
    <p class="tagline">Confidently buy or sell a local business today</p>

    <div class="person">
      <h2 class="person__name">Glen R. Harlow</h2>
      <p class="person__title">Small Business Advisor</p>
    </div>

    <ul class="contacts">
      <li>
        <svg viewBox="0 0 12 12" aria-hidden="true"><path d="M2.5 1h2l1 2.5-1.3.9a6 6 0 0 0 3.4 3.4l.9-1.3L11 7.5v2a1 1 0 0 1-1 1A9 9 0 0 1 1.5 2a1 1 0 0 1 1-1z" fill="#8dc63f"/></svg>
        (555) 806-2147
      </li>
      <li>
        <svg viewBox="0 0 12 12" aria-hidden="true"><rect x="3" y="0.8" width="6" height="10.4" rx="1" fill="none" stroke="#8dc63f" stroke-width="1.2"/><circle cx="6" cy="9.4" r="0.6" fill="#8dc63f"/></svg>
        (555) 274-3918
      </li>
      <li>
        <svg viewBox="0 0 12 12" aria-hidden="true"><rect x="0.8" y="2.3" width="10.4" height="7.4" fill="none" stroke="#8dc63f" stroke-width="1.2"/><path d="M1 2.6 6 6.6l5-4" fill="none" stroke="#8dc63f" stroke-width="1.2"/></svg>
        g.harlow@bayfieldcapitalworks.example
      </li>
      <li>
        <svg viewBox="0 0 12 12" aria-hidden="true"><g fill="none" stroke="#8dc63f" stroke-width="1.1"><circle cx="6" cy="6" r="5"/><ellipse cx="6" cy="6" rx="2.2" ry="5"/><path d="M1 6h10M2 3.5h8M2 8.5h8"/></g></svg>
        www.bayfieldcapitalworks.example
      </li>
    </ul>

    <div class="brand-graphic" role="img" aria-label="Brand graphic area in navy and green"></div>
  </section>

  <section class="card card--back" aria-label="Business card back">
    <div class="lockup">
      <span class="lockup__square" aria-hidden="true"></span>
      <div>
        <p class="company">Bayfield Capital Works, Inc</p>
        <p class="tagline">Confidently buy or sell a local business today</p>
      </div>
    </div>
  </section>

</main>
</body>
</html>
```